real esate business card with company logo and name

we need a business card design for a real esate company

The company name is Walsh & Brand Pty Ltd, and we have our logo designed and will upload. We want classic or moden feel. Black or white background. looks more textured. Should include folowinginformations
Owen Walsh and Lucy Brand
Sales Agents & Onsite Manager
p: 07 5948 2063
F: 07 5948 2174
M:0431 857 219
3/42 Marlow Crescent, FERNLEA QLD 4213

We want this business card looks professonal. Thank you in advance.

Industry/Entity Type

Real Estate Agent

Contact Information for Business Card

Owen Walsh and Lucy Brand
Onsite Manager & Sales Agents
p: 07 5948 2063
M:0431 857 219

Font styles to use
Serif

Colors
000000
fbfbfb
333333
959595

Requirements
Must have
• company logo and name, black or white back ground

```html
<!DOCTYPE html>
<html lang="en">
<head>
<meta charset="utf-8">
<title>Walsh &amp; Brand Pty Ltd — Business Card</title>
<link rel="stylesheet" href="https://fonts.googleapis.com/css2?family=Jura:wght@500&family=Source+Sans+3:wght@400;600&display=swap">
<style>
  :root {
    --backdrop: #121212;
    --card-light: #fbfbfb;
    --card-dark: #58585c;
    --tab: #555559;
    --mark: #959595;
    --ink: #333333;
    --ink-soft: #555555;
    --ink-reverse: #f4f4f4;
  }
  * { margin: 0; padding: 0; box-sizing: border-box; }
  html, body {
    width: 1200px;
    height: 900px;
    overflow: hidden;
    background: var(--backdrop);
  }
  .stage {
    position: relative;
    width: 1200px;
    height: 900px;
  }
  .card {
    position: absolute;
    top: 170px;
    width: 347px;
    height: 561px;
  }
  .card--front {
    left: 259px;
    background: var(--card-light);
    text-align: center;
    font-family: "Source Sans 3", sans-serif;
    color: var(--ink);
  }
  .card--back {
    left: 631px;
    background: var(--card-dark);
  }
  .tab {
    position: absolute;
    left: 102px;
    width: 144px;
    height: 29px;
    background: var(--tab);
  }
  .tab--top { top: 0; }
  .tab--bottom { bottom: 0; }
  .brand-square {
    position: absolute;
    left: 106px;
    top: 62px;
    width: 136px;
    height: 136px;
    background: var(--mark);
  }
  .company-name {
    position: absolute;
    left: 0;
    width: 100%;
    text-align: center;
    white-space: nowrap;
    font-family: "Jura", sans-serif;
    font-weight: 500;
    letter-spacing: 0.06em;
    text-indent: 0.06em;
    text-transform: uppercase;
  }
  .card--front .company-name {
    top: 244px;
    font-size: 17px;
    color: var(--ink-soft);
  }
  .agents {
    position: absolute;
    top: 308px;
    left: 0;
    width: 100%;
  }
  .agents__names {
    font-size: 19px;
    font-weight: 600;
    color: var(--ink-soft);
    line-height: 1.2;
  }
  .agents__role {
    font-size: 15px;
    line-height: 1.4;
  }
  .contact {
    position: absolute;
    top: 384px;
    left: 0;
    width: 100%;
    font-size: 15px;
    line-height: 23px;
  }
  .contact__line {
    display: flex;
    justify-content: center;
    align-items: center;
    gap: 6px;
  }
  .contact__icon { width: 12px; height: 13px; fill: var(--ink); }
  .address {
    position: absolute;
    top: 462px;
    left: 0;
    width: 100%;
    font-size: 15px;
    line-height: 23px;
    font-style: normal;
  }
  .back-square {
    position: absolute;
    left: 70px;
    top: 110px;
    width: 207px;
    height: 207px;
    border: 1.5px solid rgba(255,255,255,0.12);
  }
  .card--back .company-name {
    top: 432px;
    font-size: 22px;
    color: var(--ink-reverse);
  }
</style>
</head>
<body>
<main class="stage">
  <section class="card card--front" aria-label="Business card front">
    <div class="tab tab--top"></div>
    <div class="brand-square"></div>
    <h1 class="company-name">Walsh &amp; Brand Pty Ltd.</h1>
    <div class="agents">
      <p class="agents__names">Owen Walsh and Lucy Brand</p>
      <p class="agents__role">Onsite Manager &amp; Sales Agents</p>
    </div>
    <div class="contact">
      <p class="contact__line">
        <svg class="contact__icon" viewBox="0 0 24 24" aria-hidden="true"><path d="M3 8c0-3 4-5 9-5s9 2 9 5v2h-5V8H8v2H3zM6 11h12l3 9H3z"/></svg>
        <span>07 5948 2063</span>
      </p>
      <p class="contact__line">
        <svg class="contact__icon" viewBox="0 0 24 24" aria-hidden="true"><path d="M7 1h10a2 2 0 0 1 2 2v18a2 2 0 0 1-2 2H7a2 2 0 0 1-2-2V3a2 2 0 0 1 2-2zm0 3v14h10V4zm5 15.5a1 1 0 1 0 0 2 1 1 0 0 0 0-2z"/></svg>
        <span>0431 857 219</span>
      </p>
    </div>
    <address class="address">3/42 Marlow Crescent,<br>FERNLEA QLD 4213</address>
    <div class="tab tab--bottom"></div>
  </section>

  <section class="card card--back" aria-label="Business card back">
    <div class="back-square"></div>
    <p class="company-name">Walsh &amp; Brand Pty Ltd.</p>
  </section>
</main>
</body>
</html>
```